Professional Website

We are looking for a new website for our Staffing Company. Attached is a document with all the details and pages needed along with some examples of others websites.

We want a professional Look and feel around the same color theme as the attached Amber Compass.

We currently host our site on PageLoom.io. If the winning designer can also add to PageLoom, that is a plus.

```html
<!DOCTYPE html>
<html lang="en">
<head>
<meta charset="utf-8">
<title>Crestline Staffing – Recruiting Agency</title>
<link href="https://fonts.googleapis.com/css2?family=Barlow:wght@500;600;700&family=IBM+Plex+Sans:wght@400;500;600&display=swap" rel="stylesheet">
<style>
:root{
  --blue:#2438b8;
  --blue-dark:#1c2a96;
  --ink:#222;
  --text:#4a4a4a;
  --light:#f3f3f3;
  --white:#fff;
}
*{box-sizing:border-box;margin:0;padding:0}
html,body{width:1200px;height:2907px;overflow:hidden}
body{font-family:"IBM Plex Sans",sans-serif;color:var(--ink);background:var(--white);position:relative}
.abs{position:absolute}
.heading{font-family:"Barlow",sans-serif;font-weight:700;color:var(--blue);text-transform:uppercase}
.btn{display:inline-flex;align-items:center;gap:10px;height:38px;padding:0 24px;border-radius:20px;font-family:"IBM Plex Sans",sans-serif;font-weight:500;font-size:15px;text-transform:uppercase;white-space:nowrap}
.btn-outline{border:2px solid var(--blue);color:var(--ink);background:var(--white)}
.btn-solid{background:var(--blue);color:var(--white)}
.btn-white{background:var(--white);color:var(--ink)}
.chev{width:16px;height:12px}

/* top bar */
.topbar{top:0;left:0;width:1200px;height:34px;background:var(--blue)}
.social{top:9px;width:14px;height:14px;border:2px solid var(--white);border-radius:50%}
.login{top:0;height:34px;background:var(--blue-dark);color:var(--white);font-weight:500;font-size:15px;display:flex;align-items:center;justify-content:center}

/* header */
.header{top:34px;left:0;width:1200px;height:76px;background:var(--white)}
.logo-text{font-family:"IBM Plex Sans",sans-serif;font-weight:600;font-size:34px;color:var(--blue);letter-spacing:-.5px}
.nav{top:0;left:463px;height:76px;display:flex}
.nav a{display:flex;align-items:center;padding:0 15px;font-size:15px;color:var(--ink);text-decoration:none}
.nav a.active{background:#f4f4f4}
.phone{top:19px;left:900px;width:190px;height:38px;border:2px solid var(--blue);border-radius:20px;display:flex;align-items:center;justify-content:center;gap:12px;color:var(--blue);font-size:15px}

/* hero */
.hero{top:110px;left:0;width:1200px;height:599px;background:linear-gradient(90deg,#eceae6 0%,#f4f3f1 38%,#d9cfc2 40%,#e3dbd0 70%,#d8cdbf 100%)}
.hero-title{top:140px;right:110px;text-align:right;font-size:43px;line-height:54px}
.hero-sub{top:303px;right:110px;text-align:right;font-size:20px;line-height:32px;color:var(--ink)}

/* about */
.sec-title{display:flex;align-items:center;justify-content:center;gap:20px;font-size:32px}
.sec-title .q{font-size:26px}
.quote{top:866px;left:111px;border-left:2px solid var(--blue);padding-left:16px;font-size:18px;line-height:28px;font-weight:500;width:420px}
.about-copy{top:936px;left:111px;width:463px;font-size:15px;line-height:25.8px;color:var(--text);text-align:justify}
.dots{top:880px;left:622px;width:90px;height:170px;background-image:radial-gradient(#cfcfcf 1.4px,transparent 1.6px);background-size:16px 16px}

/* services */
.services{top:1280px;left:0;width:1200px;height:665px;background:var(--light)}
.card{top:157px;width:300px;height:378px;text-align:center;padding-top:40px}
.card.light{background:var(--white)}
.card.dark{background:var(--blue)}
.icon-ring{width:118px;height:118px;margin:0 auto;border-radius:50%;display:flex;align-items:center;justify-content:center}
.light .icon-ring{border:2px solid var(--blue)}
.dark .icon-ring{background:var(--white)}
.card h3{font-family:"Barlow",sans-serif;font-weight:700;font-size:21px;margin-top:26px;text-transform:uppercase}
.light h3{color:var(--blue)}
.dark h3{color:var(--white)}
.card p{font-size:15px;line-height:26px;margin:10px auto 0;width:250px}
.light p{color:var(--text)}
.dark p{color:var(--white)}
.card .btn{margin-top:16px;height:38px}

/* sales */
.check-item{left:627px;width:460px;display:flex;gap:26px}
.check-item p{font-size:15px;line-height:26px;color:var(--text)}

/* newsletter */
.news-left{top:2535px;left:0;width:1200px;height:124px;background:var(--light)}
.news-right{top:2535px;left:0;width:1200px;height:124px;background:var(--blue-dark);clip-path:polygon(370px 0,1200px 0,1200px 124px,418px 124px)}
.field{top:2574px;width:224px;height:48px;background:var(--white);display:flex;align-items:center;padding-left:18px;font-size:15px;color:#555}

/* footer */
.footer{top:2659px;left:0;width:1200px;height:248px;background:var(--blue);color:var(--white)}
.foot-row{display:flex;gap:40px;font-size:15px}
.foot-label{font-weight:600;font-size:15px;text-transform:uppercase}
</style>
</head>
<body>

<!-- top bar -->
<div class="abs topbar">
  <span class="abs social" style="left:112px"></span>
  <span class="abs social" style="left:142px"></span>
  <span class="abs social" style="left:171px"></span>
  <div class="abs login" style="left:526px;width:183px">PAYROLL BANK LOGIN</div>
  <div class="abs login" style="left:717px;width:183px">EMPLOYEE LOGIN</div>
  <div class="abs login" style="left:907px;width:183px">PAY CARD LOGIN</div>
</div>

<!-- header -->
<header class="abs header">
  <div class="abs logo-text" style="left:111px;top:14px">Crestline Staffing</div>
  <nav class="abs nav">
    <a class="active">Home</a><a>Job</a><a>About</a><a>Culture</a><a>Team</a><a>Contact</a>
  </nav>
  <div class="abs phone">
    <svg width="18" height="18" viewBox="0 0 24 24"><path d="M6.6 10.8a15 15 0 0 0 6.6 6.6l2.2-2.2c.3-.3.7-.4 1-.2 1.1.4 2.3.6 3.6.6.6 0 1 .4 1 1V20c0 .6-.4 1-1 1A17 17 0 0 1 3 4c0-.6.4-1 1-1h3.5c.6 0 1 .4 1 1 0 1.3.2 2.5.6 3.6.1.3 0 .7-.2 1z" fill="#2438b8"/></svg>
    555-010-4821
  </div>
</header>

<!-- hero -->
<section class="abs hero" role="img" aria-label="Overhead photo of two people shaking hands across a white desk with a laptop and documents, beside a light wood floor"></section>
<h1 class="abs heading hero-title">Recruiting agency for<br>temporary and direct<br>hire employees</h1>
<p class="abs hero-sub">Are you tired of the average temporary staffing<br>agency that sends unqualified&nbsp; warm bodies</p>
<a class="abs btn btn-solid" style="top:493px;left:609px;height:38px;font-size:15px">I'm looking for a job
  <svg class="chev" viewBox="0 0 16 12"><path d="M2 1l5 5-5 5M9 1l5 5-5 5" stroke="#fff" stroke-width="2.4" fill="none"/></svg></a>
<a class="abs btn btn-white" style="top:493px;left:870px">I need employees
  <svg class="chev" viewBox="0 0 16 12"><path d="M2 1l5 5-5 5M9 1l5 5-5 5" stroke="#2438b8" stroke-width="2.4" fill="none"/></svg></a>

<!-- about -->
<h2 class="abs heading sec-title" style="top:788px;left:0;width:1200px"><span class="q">«</span>About Crestline Staffing<span class="q">»</span></h2>
<p class="abs quote">Are you tired of the average temporary staffing agency that sends unqualified warm bodies?</p>
<p class="abs about-copy">Greatest part of our daily job is that we are constantly bringing people together.Our Clients come to us in search of the perfect candidate and the job hunters approach us when they are in need of a job or looking for their next exciting role.Being able to work with and connect the two is incredibly satisfying. Not to mention that in today's current job market, employers are fighting for the top talent. This makes our employees and partners grateful for</p>
<a class="abs btn btn-outline" style="top:1136px;left:111px;height:40px">Learn more
  <svg class="chev" viewBox="0 0 16 12"><path d="M2 1l5 5-5 5M9 1l5 5-5 5" stroke="#2438b8" stroke-width="2.4" fill="none"/></svg></a>
<div class="abs dots"></div>
<div class="abs" style="top:849px;left:717px;width:363px;height:307px;background:linear-gradient(135deg,#f1efe9,#e8e2d6 60%,#d9d3c8)" role="img" aria-label="Photo of hands typing on a laptop keyboard"></div>
<div class="abs" style="top:1065px;left:600px;width:177px;height:127px;background:linear-gradient(135deg,#e9ebee,#c9ccd2)" role="img" aria-label="Photo of a business handshake over a desk"></div>

<!-- services -->
<section class="abs services">
  <h2 class="abs heading sec-title" style="top:84px;left:0;width:1200px"><span class="q">«</span>Our services<span class="q">»</span></h2>

  <div class="abs card light" style="left:0">
    <div class="icon-ring"><svg width="62" height="62" viewBox="0 0 62 62" fill="none" stroke="#222" stroke-width="2.5"><path d="M10 44l14-14 8 6 18-18"/><path d="M52 44L38 30l-8 6"/><path d="M22 10l3 5M31 7v6M40 10l-3 5"/></svg></div>
    <h3>Team players</h3>
    <p>We're always willing to go the extra mile for the ofce, share the workload, and coach</p>
    <a class="btn btn-solid">Learn more</a>
  </div>
  <div class="abs card dark" style="left:300px">
    <div class="icon-ring"><svg width="62" height="62" viewBox="0 0 62 62" fill="none" stroke="#222" stroke-width="2.5"><path d="M12 14v16h12M50 48V32H38"/><path d="M24 30l8-8M38 32l-8 8"/></svg></div>
    <h3>Kind people</h3>
    <p>We NEVER talk down to others but instead choose to work harmoniously</p>
    <a class="btn btn-white">Learn more</a>
  </div>
  <div class="abs card light" style="left:599px">
    <div class="icon-ring"><svg width="62" height="62" viewBox="0 0 62 62" fill="none" stroke="#222" stroke-width="2.5"><circle cx="31" cy="20" r="7"/><circle cx="17" cy="26" r="6"/><circle cx="45" cy="26" r="6"/><path d="M19 52V40a12 12 0 0 1 24 0v12M6 52V42a10 10 0 0 1 10-8M56 52V42a10 10 0 0 0-10-8"/></svg></div>
    <h3>Hard workers</h3>
    <p>We are a team of hardworking, dedicated people who have our sights set on long-term</p>
    <a class="btn btn-solid">Learn more</a>
  </div>
  <div class="abs card dark" style="left:899px">
    <div class="icon-ring"><svg width="62" height="62" viewBox="0 0 62 62" fill="none" stroke="#222" stroke-width="2.5"><circle cx="31" cy="16" r="6"/><path d="M22 34a9 9 0 0 1 18 0"/><path d="M8 24v16l10 12M54 24v16L44 52"/><path d="M14 30l8 8M48 30l-8 8"/></svg></div>
    <h3>Family oriented</h3>
    <p>We care about your family and will help you do better for them even if this isn'</p>
    <a class="btn btn-white">Learn more</a>
  </div>

  <div class="abs" style="top:568px;left:553px;display:flex;gap:18px">
    <svg class="chev" viewBox="0 0 16 12"><path d="M2 1l5 5-5 5M9 1l5 5-5 5" stroke="#2438b8" stroke-width="2.4" fill="none"/></svg>
    <svg class="chev" viewBox="0 0 16 12"><path d="M2 1l5 5-5 5M9 1l5 5-5 5" stroke="#2438b8" stroke-width="2.4" fill="none"/></svg>
    <svg class="chev" viewBox="0 0 16 12"><path d="M2 1l5 5-5 5M9 1l5 5-5 5" stroke="#b9b9b9" stroke-width="2.4" fill="none"/></svg>
  </div>
</section>

<!-- sales & marketing -->
<div class="abs" style="top:2115px;left:0;width:37px;height:222px;background:var(--blue)"></div>
<div class="abs" style="top:2403px;left:97px;width:453px;height:43px;background:var(--blue)"></div>
<div class="abs" style="top:2036px;left:37px;width:546px;height:367px;background:linear-gradient(135deg,#e4e2de,#cfc9c0 50%,#a9a39a)" role="img" aria-label="Photo of a woman presenting at a flip chart to colleagues in an office"></div>

<h2 class="abs heading sec-title" style="top:2046px;left:627px;justify-content:flex-start"><span class="q">«</span>Sales &amp; marketing<span class="q">»</span></h2>
<div class="abs check-item" style="top:2104px">
  <svg width="24" height="24" viewBox="0 0 24 24" style="flex:none;margin-top:10px"><path d="M3 13l6 6L21 5" stroke="#2438b8" stroke-width="3" fill="none"/></svg>
  <p>First of all, we grow slow (and we like it that way). We only bring on one client at a time and make them our top priority, ensuring that they are 100% taken care of before</p>
</div>
<div class="abs check-item" style="top:2193px">
  <svg width="24" height="24" viewBox="0 0 24 24" style="flex:none;margin-top:10px"><path d="M3 13l6 6L21 5" stroke="#2438b8" stroke-width="3" fill="none"/></svg>
  <p>First of all, we grow slow (and we like it that way). We only bring on one client at a time and make them our top priority, ensuring that they are 100% taken care of before</p>
</div>
<div class="abs check-item" style="top:2281px;width:470px">
  <svg width="24" height="24" viewBox="0 0 24 24" style="flex:none;margin-top:10px"><path d="M3 13l6 6L21 5" stroke="#2438b8" stroke-width="3" fill="none"/></svg>
  <p>Crestline Staffing's sales strategy centers around relationship Instead of having designated sales representatives, our Team Leads stay incommunication importance for us; light</p>
</div>
<a class="abs btn btn-outline" style="top:2369px;left:634px;height:40px">Learn more
  <svg class="chev" viewBox="0 0 16 12"><path d="M2 1l5 5-5 5M9 1l5 5-5 5" stroke="#2438b8" stroke-width="2.4" fill="none"/></svg></a>

<!-- newsletter -->
<div class="abs news-left"></div>
<div class="abs news-right"></div>
<h2 class="abs heading" style="top:2557px;left:109px;font-size:32px;line-height:38px">Sign up to<br>our newsletter</h2>
<div class="abs field" style="left:438px">Name</div>
<div class="abs field" style="left:674px">Email</div>
<div class="abs" style="top:2574px;left:910px;width:178px;height:48px;background:var(--blue);color:var(--white);display:flex;align-items:center;justify-content:center;font-weight:600;font-size:15px">SUBSCRIBE</div>

<!-- footer -->
<footer class="abs footer">
  <div class="abs foot-label" style="top:76px;left:111px">Quick link</div>
  <div class="abs foot-row" style="top:76px;left:292px"><span>Home</span><span>Job</span><span>About</span><span>Culture</span><span>Team</span><span>Contact</span></div>
  <div class="abs foot-label" style="top:111px;left:109px">Areas we service</div>
  <div class="abs foot-row" style="top:111px;left:292px"><span>Northgate</span><span>Elm Ridge</span><span>Harbor Falls</span></div>
  <div class="abs" style="top:60px;left:840px;font-weight:600;font-size:34px;letter-spacing:-.5px">Crestline Staffing</div>
  <div class="abs" style="top:167px;left:0;width:1200px;height:1px;background:rgba(255,255,255,.35)"></div>
  <div class="abs" style="top:203px;left:107px;font-size:15px">Copy Rights @ 2022 Crestline Staffing All Rights Reserved</div>
  <div class="abs" style="top:203px;left:913px;font-size:15px">Hotline # 555-010-7730</div>
</footer>

</body>
</html>
```